Redesign of business card for Cedar Ridge Mechanical

We are looking for a new design for our business cards for Cedar Ridge Mechanical. We are a plumbing & HVAC construction company, operating on the West Coast of Canada and USA. Logo attached.
Industry/Entity Type
Construction - Plumbing & HVAC
Contact Information for Business Card
Name, address, phone numbers, email, website address
Look and feel
Each slider illustrates characteristics of the customer's brand and the style your logo design should communicate.

```html
<!DOCTYPE html>
<html lang="en">
<head>
<meta charset="utf-8">
<title>Cedar Ridge Mechanical — Business Card</title>
<link href="https://fonts.googleapis.com/css2?family=Poppins:wght@300;400;500;600;700&display=swap" rel="stylesheet">
<style>
  :root {
    --page: #d9d6d0;
    --card-edge: #0b0b0b;
    --card-face: #e4e5e5;
    --ink: #0d0d0d;
    --emboss: #d3d4d4;
    --emboss-light: #f3f3f3;
    --notch: #f4f4f4;
  }
  * { margin: 0; padding: 0; box-sizing: border-box; }
  html, body { width: 1200px; height: 711px; overflow: hidden; }
  body {
    background: var(--page);
    font-family: "Poppins", sans-serif;
    color: var(--ink);
    display: flex;
    align-items: center;
    justify-content: center;
    gap: 40px;
  }
  .card {
    position: relative;
    width: 540px;
    height: 320px;
    background: var(--card-edge);
    border-radius: 22px;
    padding: 14px;
  }
  .card__face {
    position: relative;
    width: 100%;
    height: 100%;
    background: var(--card-face);
    border-radius: 12px;
    overflow: hidden;
  }
  .notch {
    position: absolute;
    width: 3px;
    height: 14px;
    background: var(--notch);
  }
  .notch--tl { top: 0; left: 28px; }
  .notch--tr { top: 0; right: 28px; }
  .notch--bl { bottom: 0; left: 28px; }
  .notch--br { bottom: 0; right: 28px; }

  /* Back */
  .back__mark {
    position: absolute;
    inset: 0;
    display: flex;
    align-items: center;
    justify-content: center;
    gap: 12px;
    font-weight: 600;
    font-size: 26px;
    letter-spacing: 0.5px;
    color: var(--emboss);
    text-shadow: 1px 1px 0 var(--emboss-light);
  }
  .back__square {
    width: 26px; height: 26px;
    background: var(--emboss);
  }

  /* Front */
  .front__brand {
    position: absolute;
    top: 56px;
    right: 26px;
    width: 230px;
    display: flex;
    align-items: center;
    gap: 10px;
    font-weight: 600;
    font-size: 22px;
    line-height: 1.15;
  }
  .front__square {
    flex: none;
    width: 34px; height: 34px;
    background: var(--ink);
  }
  .front__details {
    position: absolute;
    left: 26px;
    bottom: 22px;
  }
  .person__name { font-size: 24px; line-height: 1.1; }
  .person__first { font-weight: 700; }
  .person__last { font-weight: 300; }
  .person__role { font-size: 12px; font-weight: 500; margin-bottom: 10px; }
  .address { font-size: 12px; line-height: 1.35; margin-bottom: 8px; }
  .contact-list { list-style: none; font-size: 12.5px; line-height: 1.55; }
  .contact-list li { display: flex; align-items: center; gap: 8px; }
  .contact-list svg { width: 12px; height: 12px; flex: none; fill: var(--ink); }
</style>
</head>
<body>

  <section class="card card--back" aria-label="Card back">
    <span class="notch notch--tl"></span><span class="notch notch--tr"></span>
    <span class="notch notch--bl"></span><span class="notch notch--br"></span>
    <div class="card__face">
      <div class="back__mark">
        <span class="back__square"></span>
        <span>Cedar Ridge Mechanical</span>
      </div>
    </div>
  </section>

  <section class="card card--front" aria-label="Card front">
    <span class="notch notch--tl"></span><span class="notch notch--tr"></span>
    <span class="notch notch--bl"></span><span class="notch notch--br"></span>
    <div class="card__face">
      <div class="front__brand">
        <span class="front__square"></span>
        <span>Cedar Ridge Mechanical</span>
      </div>

      <div class="front__details">
        <p class="person__name"><span class="person__first">Marta</span> <span class="person__last">Kovacs</span></p>
        <p class="person__role">Founder &amp; CEO</p>
        <p class="address">4720 Alder Way Suite 210<br>Portland, OR 97204</p>
        <ul class="contact-list">
          <li>
            <svg viewBox="0 0 24 24" aria-hidden="true"><path d="M6.6 10.8a15.1 15.1 0 0 0 6.6 6.6l2.2-2.2c.3-.3.7-.4 1-.2 1.1.4 2.3.6 3.6.6.6 0 1 .4 1 1V20c0 .6-.4 1-1 1C10.6 21 3 13.4 3 4c0-.6.4-1 1-1h3.5c.6 0 1 .4 1 1 0 1.3.2 2.5.6 3.6.1.3 0 .7-.2 1L6.6 10.8z"/></svg>
            <span>(503) 555-0147</span>
          </li>
          <li>
            <svg viewBox="0 0 24 24" aria-hidden="true"><path d="M12 2a10 10 0 1 0 0 20 10 10 0 0 0 0-20zm-1 17.9A8 8 0 0 1 4.1 11H7c.1 3.3 1.5 6.3 4 8.9zm0-10.9H6.9c.2-2.7 1.3-5.3 3.1-7.1A8 8 0 0 1 11 9zm2 0V3.1A8 8 0 0 1 19.9 11H17c-.1-.7-.2-1.4-.4-2H13zm0 2h4c-.2 3.1-1.6 6-4 8.2V11z"/></svg>
            <span>info@yourwebsite.com</span>
          </li>
          <li>
            <svg viewBox="0 0 24 24" aria-hidden="true"><path d="M3 5h18c.6 0 1 .4 1 1v12c0 .6-.4 1-1 1H3c-.6 0-1-.4-1-1V6c0-.6.4-1 1-1zm9 7.5L4 7v10h16V7l-8 5.5z"/></svg>
            <span>www.yourwebsite.com</span>
          </li>
        </ul>
      </div>
    </div>
  </section>

</body>
</html>
```